Quorva - corporate Business Card

We need a good look and innovative business card for a new start up company based in Los Angeles called "Quorva". We are in a payment business, including payment card, app, and ewallet. We are expert in online payment and Card not present (CNP) transaction.
We need an innovative, modern business card.

Our logo font is Aero Matics

Target Market(s)

Startup - Bank - Online Payment - Card Manufacturing

Industry/Entity Type

Startup

Contact Information for Business Card

phone: 555 014 7396 - Address: 4172 Marlowe blvd, Cylver City, CA 90299

Requirements
Must have
• Message: innovative, professional, expert, high tech, trust, online payment expert, security
Nice to have
• no comment
Should not have
• no Comment

```html
<!DOCTYPE html>
<html lang="en">
<head>
<meta charset="utf-8">
<title>Quorva — Business Card</title>
<link rel="stylesheet" href="https://fonts.googleapis.com/css2?family=Oswald:wght@500&family=Open+Sans:wght@300;400;600&display=swap">
<style>
  :root {
    --backdrop: #2b2b2b;
    --card: #232323;
    --card-edge: #1b1b1b;
    --mark: #1a1a1a;
    --wordmark: #cfcfcf;
    --ink: #ffffff;
    --ink-soft: #d6d6d6;
    --accent: #b11e2a;
    --rule: #6a6a6a;
  }
  * { box-sizing: border-box; margin: 0; padding: 0; }
  html, body {
    width: 1200px; height: 1000px; overflow: hidden;
    background: var(--backdrop);
  }
  .sheet {
    position: relative; width: 1200px; height: 1000px;
    display: flex; flex-direction: column; align-items: center; justify-content: center;
    gap: 56px;
  }
  .card {
    position: relative; width: 760px; height: 434px;
    background: var(--card);
    border: 1px solid var(--card-edge);
    box-shadow: 0 10px 30px rgba(0,0,0,0.45);
  }
  /* Front */
  .card--front { display: flex; align-items: center; justify-content: center; gap: 22px; }
  .brand-dot {
    width: 78px; height: 78px; border-radius: 50%;
    background: var(--mark);
    box-shadow: inset 0 2px 6px rgba(0,0,0,0.6);
  }
  .brand-name {
    font-family: "Open Sans", sans-serif; font-weight: 600;
    font-size: 74px; letter-spacing: 1px; color: var(--wordmark);
    line-height: 1;
  }
  /* Back */
  .card--back { display: flex; align-items: center; padding-left: 56px; padding-top: 40px; }
  .identity { text-align: right; white-space: nowrap; padding-right: 22px; }
  .identity__name {
    font-family: "Oswald", sans-serif; font-weight: 500;
    font-size: 44px; line-height: 1.05; color: var(--ink); letter-spacing: 0.5px;
    text-transform: uppercase;
  }
  .identity__role {
    font-family: "Open Sans", sans-serif; font-weight: 600;
    font-size: 21px; color: var(--accent); text-transform: uppercase; letter-spacing: 0.5px;
    margin-top: 2px;
  }
  .divider { width: 1px; height: 124px; background: var(--rule); flex: none; }
  .contact { padding-left: 24px; font-family: "Open Sans", sans-serif; font-weight: 300; color: var(--ink-soft); white-space: nowrap; }
  .contact__address { font-size: 18px; line-height: 1.25; letter-spacing: 0.8px; margin-left: 30px; margin-bottom: 6px; }
  .contact__row { display: flex; align-items: center; gap: 14px; font-size: 19px; line-height: 1.45; letter-spacing: 0.6px; }
  .contact__icon { width: 16px; height: 16px; flex: none; }
  .contact__highlight { color: var(--accent); }
</style>
</head>
<body>
<main class="sheet">
  <section class="card card--front" aria-label="Card front">
    <span class="brand-dot"></span>
    <span class="brand-name">Quorva</span>
  </section>

  <section class="card card--back" aria-label="Card back">
    <div class="identity">
      <h1 class="identity__name">Daniel Reyes</h1>
      <p class="identity__role">CEO &amp; Founder</p>
    </div>
    <span class="divider"></span>
    <div class="contact">
      <p class="contact__address">4172 Marlowe blvd,<br>Halden City, CA 90299</p>
      <p class="contact__row">
        <svg class="contact__icon" viewBox="0 0 16 16" aria-hidden="true"><path fill="#b11e2a" d="M3.6 1.5l2.2 2.6-1.3 1.6c.8 1.8 2.1 3.1 3.9 3.9l1.6-1.3 2.6 2.2-1.3 2.3C6.7 12.6 3.4 9.3 1.3 2.8z"/></svg>
        555 014 7396
      </p>
      <p class="contact__row">
        <svg class="contact__icon" viewBox="0 0 16 16" aria-hidden="true"><rect x="1" y="3" width="14" height="10" fill="#b11e2a"/><path d="M1.5 3.5L8 9l6.5-5.5" stroke="#232323" stroke-width="1.4" fill="none"/></svg>
        yourname@email.com
      </p>
      <p class="contact__row">
        <svg class="contact__icon" viewBox="0 0 16 16" aria-hidden="true"><circle cx="8" cy="8" r="7" fill="#b11e2a"/><path d="M1 8h14M8 1c-3 3.5-3 10.5 0 14M8 1c3 3.5 3 10.5 0 14" stroke="#232323" stroke-width="1" fill="none"/></svg>
        <span>www.<span class="contact__highlight">websitename</span>.com</span>
      </p>
    </div>
  </section>
</main>
</body>
</html>
```